Tovel & Associates - London New Letting and Property Management Company *

Tovel & Associates LTD is a new company based in London, and works with brand new residential property in the city centre.

We are aiming to have 1000 new properties a year.

We are looking for something modern and minimalistic :
Logo ,Monogram, Paper Head and Business Card.

Target Market(s)

Internation landlords

Industry/Entity Type

Real Estate

Logo Text

Tovel & Associates

Colors

Designer to choose colors to be used in the design.

Requirements
Nice to have
• A particular monogram with "TA"
Should not have
• Little House over the logo

```html
<!DOCTYPE html>
<html lang="en">
<head>
<meta charset="utf-8">
<title>Tovel &amp; Associates – Stationery</title>
<link href="https://fonts.googleapis.com/css2?family=Work+Sans:wght@400;500;600&display=swap" rel="stylesheet">
<style>
:root{
  --bg:#dcdcdc;
  --paper:#f3f3f3;
  --card:#f4f4f4;
  --navy:#1b4e70;
  --sky:#29a7df;
  --ink:#5a5a5a;
  --ink-dark:#3e3e3e;
}
*{margin:0;padding:0;box-sizing:border-box}
html,body{width:1200px;height:1062px;overflow:hidden;background:var(--bg);font-family:"Work Sans",sans-serif;color:var(--ink)}
.stage{position:relative;width:1200px;height:1062px}
.sheet{position:absolute;background:var(--paper);box-shadow:0 2px 8px rgba(0,0,0,.18);overflow:hidden}
.letterhead{left:115px;top:94px;width:620px;height:876px}
.brand-mark{display:block;background:var(--navy)}
.brand-name{font-family:"Work Sans",sans-serif;font-weight:600;color:var(--navy);text-transform:uppercase;white-space:nowrap;letter-spacing:.3px}
.lh-logo{position:absolute;right:44px;top:36px;display:flex;flex-direction:column;align-items:flex-end}
.lh-logo .brand-mark{width:106px;height:106px}
.lh-logo .brand-name{font-size:10px;margin-top:10px}
.salutation{position:absolute;left:45px;top:178px;font-size:17px;color:var(--ink)}
.body-copy{position:absolute;left:45px;top:232px;width:535px;font-size:11.7px;line-height:16.2px;letter-spacing:-.05px;color:var(--ink)}
.body-copy p{margin-bottom:20px}
.closing{position:absolute;left:45px;top:614px;font-size:14.5px;color:var(--ink)}
.signature{position:absolute;left:45px;top:644px;width:112px;height:20px;background:linear-gradient(90deg,rgba(90,90,90,.25),rgba(90,90,90,.08))}
.signer{position:absolute;left:45px;top:674px;color:var(--ink-dark)}
.signer .name{font-size:13.5px}
.signer .role{font-size:11.5px;margin-top:1px}
.signer .company{font-size:8px;font-weight:500;text-transform:uppercase;margin-top:6px}
.rule{position:absolute;height:2px;background:var(--navy)}
.lh-rule{left:39px;top:771px;width:537px}
.contact{position:absolute;list-style:none}
.contact li{display:flex;align-items:center;gap:6px;white-space:nowrap}
.contact svg{flex:none}
.lh-contact{left:39px;top:795px;font-size:12px;line-height:15.2px}
.web b{color:var(--navy);font-weight:500}
.wave{position:absolute;left:0;bottom:0;width:100%}
.address{position:absolute;color:#fff;white-space:nowrap}
.lh-address{right:44px;bottom:16px;font-size:12px}

.hero-logo{position:absolute;left:878px;top:152px;display:flex;flex-direction:column;align-items:center}
.hero-logo .brand-mark{width:212px;height:212px}
.hero-logo .brand-name{font-size:18px;margin-top:14px;letter-spacing:.6px}

.card-front{left:716px;top:475px;width:374px;height:213px;background:var(--card)}
.cf-logo{position:absolute;left:17px;top:14px;display:flex;flex-direction:column;align-items:flex-start}
.cf-logo .brand-mark{width:90px;height:90px}
.cf-logo .brand-name{font-size:8px;margin-top:6px}
.person{position:absolute;right:17px;top:103px;text-align:right}
.person .name{font-size:14.5px;font-weight:500;color:var(--navy);letter-spacing:.3px;text-transform:uppercase}
.person .role{font-size:9px;color:var(--ink);margin-top:2px}
.cf-rule{left:17px;top:141px;width:340px;height:1.5px}
.cf-contact{left:17px;top:152px;font-size:9.2px;line-height:13px}
.cf-address{right:17px;bottom:6px;font-size:9px}

.card-back{left:717px;top:727px;width:373px;height:212px;background:var(--navy)}
.cb-logo{position:absolute;left:0;right:0;top:48px;display:flex;flex-direction:column;align-items:center}
.cb-logo .brand-mark{width:101px;height:101px;background:#fff}
.cb-logo .brand-name{font-size:9.5px;margin-top:9px;color:#fff}
</style>
</head>
<body>
<main class="stage">

  <section class="sheet letterhead" aria-label="Letterhead">
    <div class="lh-logo">
      <span class="brand-mark" aria-hidden="true"></span>
      <span class="brand-name">Tovel &amp; Associates</span>
    </div>
    <p class="salutation">Dear Sir</p>
    <div class="body-copy">
      <p>Lorem ipsum dolor sit amet, an vel recteque dissentiet, detracto albucius platonem ex vel, eros repudiandae cu. Atqui aliquando nec an, unum graece adolescens vel ad. Id odio scae has, iudico euismod atomorum ius ea, cum ea honestatis quaerendum theophrastus. Mea honestatis quaerendum theophrastus. Mea</p>
      <p>Lorem ipsum dolor sit amet, an vel recteque dissentiet, detracto albucius platonem ex vel, eros repudiandae cu. Atqui aliquando nec an, unum graece adolescens vel ad. Id odio scae has, iudico euismod atomorum ius ea, cum ea honestatis quaerendum theophrastus. Mea doming repudiandae ex, cu cum civibus assentior posidonium. Quo etiam pertinax ex, te eros repudiandae cu. Atqui aliquando nec an, unum graece adolescens vel ad. Id odio scae honestatis quaerendum theophrastus. Mea</p>
      <p>Lorem ipsum dolor sit amet, an vel recteque dissentiet, detracto albucius platonem ex vel, eros repudiandae cu. Atqui aliquando nec an, unum graece adolescens vel ad. Id odio scae has, iudico euismod atomorum ius ea, cum ea honestatis quaerendum theophrastus. Mea honestatis quaerendum theophrastus. Mea</p>
      <p>Lorem ipsum dolor sit amet, an vel recteque dissentiet, detracto albucius platonem ex vel, eros repudiandae cu. Atqui aliquando nec an, unum graece adolescens vel ad. Id odio scae has, iudico euismod atomorum ius ea, cum ea honestatis quaerendum theophrastus. Mea honestatis quaerendum theophrastus. Mea</p>
    </div>
    <p class="closing">Kind Regards</p>
    <div class="signature" role="img" aria-label="Handwritten signature"></div>
    <div class="signer">
      <p class="name">Oliver Brantley</p>
      <p class="role">Chief Alchemist</p>
      <p class="company">Northgate Estate Holdings LTD</p>
    </div>
    <div class="rule lh-rule"></div>
    <ul class="contact lh-contact">
      <li><svg width="8" height="8" viewBox="0 0 10 10"><path d="M2 1 L4 1 L4.6 3.4 L3.4 4.3 Q4.5 6 6 6.6 L6.8 5.4 L9 6 L9 8 Q5 9.5 1 4 Z" fill="var(--navy)"/></svg><span>+44 20 7946 0321</span></li>
      <li><svg width="8" height="8" viewBox="0 0 10 10"><rect x="1" y="2.5" width="8" height="5.5" fill="none" stroke="var(--navy)" stroke-width="1.3"/><path d="M1 2.5 L5 5.5 L9 2.5" fill="none" stroke="var(--navy)" stroke-width="1.1"/></svg><span>info@tovelassociates.com</span></li>
      <li class="web"><svg width="8" height="8" viewBox="0 0 10 10"><circle cx="5" cy="5" r="4" fill="var(--navy)"/></svg><span>www.<b>tovelassociates</b>.com</span></li>
    </ul>
    <svg class="wave" width="620" height="80" viewBox="0 0 620 80" preserveAspectRatio="none" aria-hidden="true">
      <path d="M150 80 Q330 0 620 16 L620 80 Z" fill="var(--sky)"/>
      <path d="M250 80 Q405 16 620 22 L620 80 Z" fill="#fff"/>
      <path d="M260 80 Q410 22 620 28 L620 80 Z" fill="var(--navy)"/>
    </svg>
    <p class="address lh-address">14 Harlow Street London W1 4QR</p>
  </section>

  <div class="hero-logo">
    <span class="brand-mark" aria-hidden="true"></span>
    <span class="brand-name">Tovel &amp; Associates</span>
  </div>

  <section class="sheet card-front" aria-label="Business card front">
    <div class="cf-logo">
      <span class="brand-mark" aria-hidden="true"></span>
      <span class="brand-name">Tovel &amp; Associates</span>
    </div>
    <div class="person">
      <p class="name">Daniel Greaves</p>
      <p class="role">Director</p>
    </div>
    <div class="rule cf-rule"></div>
    <ul class="contact cf-contact">
      <li><svg width="6" height="6" viewBox="0 0 10 10"><path d="M2 1 L4 1 L4.6 3.4 L3.4 4.3 Q4.5 6 6 6.6 L6.8 5.4 L9 6 L9 8 Q5 9.5 1 4 Z" fill="var(--navy)"/></svg><span>+44 20 7946 0321</span></li>
      <li><svg width="6" height="6" viewBox="0 0 10 10"><rect x="1" y="2.5" width="8" height="5.5" fill="none" stroke="var(--navy)" stroke-width="1.3"/><path d="M1 2.5 L5 5.5 L9 2.5" fill="none" stroke="var(--navy)" stroke-width="1.1"/></svg><span>info@tovelassociates.com</span></li>
      <li class="web"><svg width="6" height="6" viewBox="0 0 10 10"><circle cx="5" cy="5" r="4" fill="var(--navy)"/></svg><span>www.<b>tovelassociates</b>.com</span></li>
    </ul>
    <svg class="wave" width="374" height="46" viewBox="0 0 374 46" preserveAspectRatio="none" aria-hidden="true">
      <path d="M70 46 Q210 -4 374 5 L374 46 Z" fill="var(--sky)"/>
      <path d="M124 46 Q236 6 374 10 L374 46 Z" fill="#fff"/>
      <path d="M130 46 Q240 10 374 14 L374 46 Z" fill="var(--navy)"/>
    </svg>
    <p class="address cf-address">14 Harlow Street London W1 4QR</p>
  </section>

  <section class="sheet card-back" aria-label="Business card back">
    <div class="cb-logo">
      <span class="brand-mark" aria-hidden="true"></span>
      <span class="brand-name">Tovel &amp; Associates</span>
    </div>
  </section>

</main>
</body>
</html>
```